Classy, Elegant, Simple Business Card Design

Looking to have a classy, simple, and elegant design. Want a top notch designed business card. I really like the look of the new torvane credit card. I also like the design I attached. I am trying to reach 21-29 year old females for booking us for there wedding or event. We offer Disc Jockey Service, Photo Booth Rentals, and Uplighting .

Target Market(s)

21-28 year old females

Contact Information for Business Card

Has to have logo, website, email, and phone number

Font styles to use
Other font styles liked:
• open to font choice, modern, clean
Designer to choose
33a6d7
0791cd
0555a3
ffffff

Requirements
Must have
• Has to have logo, website, email, and phone number
Nice to have
• I really like the design of the new torvane credit card. I also included my logo and some designs I like
Should not have
• clutter or too much info

```html
<!DOCTYPE html>
<html lang="en">
<head>
<meta charset="utf-8">
<title>Brightline Events – Business Card</title>
<link href="https://fonts.googleapis.com/css2?family=Poppins:wght@400;500&display=swap" rel="stylesheet">
<style>
  :root {
    --page-bg: #1e1e1e;
    --card-white: #ffffff;
    --brand-blue: #0791cd;
    --brand-deep: #0555a3;
    --brand-light: #33a6d7;
    --text-grey: #4a4a4a;
    --muted-grey: #8a8a8a;
    --rule-grey: #9a9a9a;
  }
  * { margin: 0; padding: 0; box-sizing: border-box; }
  html, body {
    width: 1200px; height: 1200px; overflow: hidden;
    background: var(--page-bg);
    font-family: "Poppins", sans-serif;
  }
  .card {
    position: absolute;
    left: 257px;
    width: 686px;
    height: 392px;
  }
  .card-front { top: 165px; background: var(--card-white); }
  .card-back {
    top: 653px;
    background: radial-gradient(ellipse at 50% 42%, #08a9e6 0%, #1592d6 55%, #1a7ec8 100%);
  }
  .brand-mark {
    position: absolute;
    left: 48px; top: 112px;
    display: flex; align-items: center; gap: 14px;
  }
  .brand-dot {
    width: 34px; height: 34px; border-radius: 50%;
    background: var(--brand-blue);
  }
  .brand-name {
    font-weight: 500; font-size: 30px; color: var(--brand-blue);
    letter-spacing: 0.5px;
  }
  .person {
    position: absolute; left: 416px; top: 222px;
  }
  .person-name {
    font-weight: 500; font-size: 25px; color: var(--brand-blue);
    line-height: 1.2; letter-spacing: 0.3px;
  }
  .person-title {
    font-weight: 400; font-size: 16px; color: var(--muted-grey);
    line-height: 1.2;
  }
  .divider {
    position: absolute; left: 416px; right: 0; top: 281px;
    height: 1px; background: var(--rule-grey);
  }
  .contacts {
    position: absolute; left: 416px; top: 294px;
    list-style: none;
  }
  .contacts li {
    display: flex; align-items: center; gap: 8px;
    font-size: 16px; color: var(--text-grey); line-height: 20px;
  }
  .contacts svg { width: 13px; height: 13px; fill: var(--brand-blue); flex: none; }
  .back-name {
    position: absolute; left: 0; right: 0; top: 160px;
    display: flex; justify-content: center; align-items: center; gap: 18px;
  }
  .back-name .brand-dot { width: 46px; height: 46px; background: #e4e8ec; }
  .back-name span {
    font-weight: 500; font-size: 52px; color: #e4e8ec; letter-spacing: 1px;
  }
  .services {
    position: absolute; left: 0; right: 0; top: 336px;
    text-align: center; color: #ffffff; font-weight: 500; font-size: 16px;
  }
</style>
</head>
<body>
  <section class="card card-front">
    <div class="brand-mark">
      <div class="brand-dot"></div>
      <div class="brand-name">Brightline Events</div>
    </div>
    <div class="person">
      <div class="person-name">Daniel Reyes</div>
      <div class="person-title">President</div>
    </div>
    <div class="divider"></div>
    <ul class="contacts">
      <li><svg viewBox="0 0 24 24"><path d="M6.6 10.8a15 15 0 0 0 6.6 6.6l2.2-2.2c.3-.3.7-.4 1-.2 1.1.4 2.3.6 3.6.6.6 0 1 .4 1 1V20c0 .6-.4 1-1 1A17 17 0 0 1 3 4c0-.6.4-1 1-1h3.5c.6 0 1 .4 1 1 0 1.3.2 2.5.6 3.6.1.3 0 .7-.2 1z"/></svg>555-214-0187</li>
      <li><svg viewBox="0 0 24 24"><path d="M2 5h20v14H2z M4 7v.5l8 5 8-5V7l-8 5z" fill-rule="evenodd"/></svg>info@brightlineevents.com</li>
      <li><svg viewBox="0 0 24 24"><circle cx="12" cy="12" r="10"/><path d="M7 8c2 0 3 1 3 3s2 2 2 4-1 3-2 5M14 4c0 2 2 3 4 3" stroke="#fff" stroke-width="1.6" fill="none"/></svg>www.brightlineevents.com</li>
    </ul>
  </section>

  <section class="card card-back">
    <div class="back-name">
      <div class="brand-dot"></div>
      <span>Brightline</span>
    </div>
    <p class="services">Disc Jockey Service • Photo Booth Rentals • Uplighting .</p>
  </section>
</body>
</html>
```